SkyvornQ Business Cards and Stationary Design

Need a design for our business cards and stationary. I want to carry on the theme of the logo. I want the business cards to have a design on the back. I would like the business cards and the stationary to carry the same theme, design scheme, and branding

Target Market(s)

Airlines and Maintenance Facilities

Industry/Entity Type

Aviation

Contact Information for Business Card

Name
Position Title
Address: 4827 Trellis Hollow Road, Fort Pierce, Florida, 34951
Office Number
Mobile Number
Email
Website

Font styles to use
Serif
Sans Serif

Colors

Designer to choose colors to be used in the design.

```html
<!DOCTYPE html>
<html lang="en">
<head>
<meta charset="utf-8">
<title>SkyvornQ Business Card</title>
<link rel="stylesheet" href="https://fonts.googleapis.com/css2?family=Roboto:wght@400;500;700;900&family=Roboto+Condensed:wght@400;700&display=swap">
<style>
  :root {
    --page-bg: #e8e6e2;
    --card-white: #f4f4f4;
    --navy: #122c57;
    --navy-deep: #0c2249;
    --navy-soft: #3b5682;
    --brand-blue: #2a8fdb;
    --sky-light: #0aa2e8;
    --sky-deep: #0a3884;
    --ink-white: #ffffff;
    --ink-mute: #d8e2f0;
  }
  * { box-sizing: border-box; margin: 0; padding: 0; }
  html, body {
    width: 1200px; height: 950px; overflow: hidden;
    background: var(--page-bg);
    font-family: "Roboto", Arial, sans-serif;
  }
  .sheet {
    position: relative; width: 1200px; height: 950px;
  }
  .card {
    position: absolute; left: 320px;
    width: 560px; height: 320px;
    border-radius: 18px; overflow: hidden;
    box-shadow: 0 10px 28px rgba(0,0,0,.18);
  }
  /* ---------- front ---------- */
  .card-front { top: 110px; background: var(--card-white); }
  .brand-lockup {
    position: absolute; left: 0; right: 0; top: 44px;
    display: flex; flex-direction: column; align-items: center; gap: 12px;
  }
  .brand-dot {
    width: 52px; height: 52px; border-radius: 50%;
    border: 5px solid var(--brand-blue);
  }
  .brand-name {
    font-family: "Roboto", Arial, sans-serif;
    font-weight: 900; font-size: 30px; letter-spacing: 9px;
    color: var(--navy); text-transform: uppercase;
  }
  .contact-band {
    position: absolute; left: 0; right: 0; bottom: 0; height: 128px;
    background: linear-gradient(90deg, var(--navy-soft) 0%, var(--navy) 45%, var(--navy-deep) 100%);
    color: var(--ink-white);
    font-family: "Roboto Condensed", Arial, sans-serif;
  }
  .person {
    position: absolute; left: 30px; top: 24px;
  }
  .person-name {
    font-weight: 700; font-size: 22px; letter-spacing: .5px; text-transform: uppercase;
  }
  .person-role { font-size: 15px; margin-top: 2px; }
  .person-address { font-size: 14px; line-height: 1.35; margin-top: 6px; color: var(--ink-mute); }
  .contact-list {
    position: absolute; right: 26px; top: 22px;
    list-style: none; text-align: right; font-size: 14.5px; line-height: 1.42;
  }
  .contact-list li { display: flex; align-items: center; justify-content: flex-end; gap: 8px; }
  .contact-list svg { width: 12px; height: 12px; fill: var(--ink-white); flex: none; }
  /* ---------- back ---------- */
  .card-back {
    top: 500px;
    background: radial-gradient(ellipse at 58% 45%, var(--sky-light) 0%, #0a6cc4 45%, var(--sky-deep) 100%);
  }
  .back-ring {
    position: absolute; left: 250px; top: 22px;
    width: 250px; height: 250px; border-radius: 50%;
    border: 22px solid rgba(255,255,255,.09);
  }
  .back-brand {
    position: absolute; left: 38px; bottom: 36px; color: var(--ink-white);
  }
  .back-name {
    font-weight: 900; font-size: 30px; letter-spacing: 8px; text-transform: uppercase;
  }
  .back-web {
    font-family: "Roboto Condensed", Arial, sans-serif;
    font-size: 13px; letter-spacing: 6px; margin-top: 6px;
  }
</style>
</head>
<body>
<main class="sheet">
  <section class="card card-front">
    <div class="brand-lockup">
      <span class="brand-dot"></span>
      <span class="brand-name">SkyvornQ</span>
    </div>
    <div class="contact-band">
      <div class="person">
        <p class="person-name">Dana Merrow</p>
        <p class="person-role">CEO/FOUNDER</p>
        <p class="person-address">4827 Trellis Hollow Road<br>Fort Pierce, Florida, 34951</p>
      </div>
      <ul class="contact-list">
        <li>772 514 0863
          <svg viewBox="0 0 24 24"><path d="M6.6 10.8a15 15 0 0 0 6.6 6.6l2.2-2.2c.3-.3.7-.4 1-.2 1.1.4 2.3.6 3.6.6.6 0 1 .4 1 1V20c0 .6-.4 1-1 1A17 17 0 0 1 3 4c0-.6.4-1 1-1h3.5c.6 0 1 .4 1 1 0 1.3.2 2.5.6 3.6.1.3 0 .7-.2 1z"/></svg>
        </li>
        <li>772 903 4417
          <svg viewBox="0 0 24 24"><path d="M7 1h10a2 2 0 0 1 2 2v18a2 2 0 0 1-2 2H7a2 2 0 0 1-2-2V3a2 2 0 0 1 2-2zm0 3v15h10V4z"/></svg>
        </li>
        <li>info@skyvornq.com
          <svg viewBox="0 0 24 24"><path d="M2 5h20v14H2zm2 2v.4l8 5 8-5V7zm0 2.8V17h16V9.8l-8 5z"/></svg>
        </li>
        <li>www.skyvornq.com
          <svg viewBox="0 0 24 24"><path d="M12 2a10 10 0 1 0 0 20 10 10 0 0 0 0-20zm6.9 9h-3a15 15 0 0 0-1.3-6A8 8 0 0 1 18.9 11zM12 4.1c.9 1.3 1.7 3.5 1.9 6.9h-3.8c.2-3.4 1-5.6 1.9-6.9zM9.4 5a15 15 0 0 0-1.3 6h-3A8 8 0 0 1 9.4 5zM5.1 13h3a15 15 0 0 0 1.3 6A8 8 0 0 1 5.1 13zm6.9 6.9c-.9-1.3-1.7-3.5-1.9-6.9h3.8c-.2 3.4-1 5.6-1.9 6.9zm2.6-.9a15 15 0 0 0 1.3-6h3a8 8 0 0 1-4.3 6z"/></svg>
        </li>
      </ul>
    </div>
  </section>

  <section class="card card-back">
    <span class="back-ring"></span>
    <div class="back-brand">
      <p class="back-name">SkyvornQ</p>
      <p class="back-web">www.skyvornq.com</p>
    </div>
  </section>
</main>
</body>
</html>
```